Website for new child psychology practice

New clinical psychology practice in NSW Australia, specialising in work with children, adolescents and families. I would like to feature the colours in the logo, which was recently designed by pixelharbor designer Odette.
I am seeking a professional looking page, which is easy to navigate and is colourful and playful but not childish.
Target Market(s)
Parents and professionals
Industry/Entity Type
Health
Coding
Coded - Design and coding required
Number of Pages Required
1 page
Font styles to use
Serif
Requirements
Must have
- Pages for 'About us' 'Services' 'Fees and information' 'Contact us'
Should not have
- Childish stock photos

```html
<!DOCTYPE html>
<html lang="en">
<head>
<meta charset="utf-8">
<title>Dr Clara Hayes – Clinical Psychologist</title>
<link rel="stylesheet" href="https://fonts.googleapis.com/css2?family=Cormorant+Garamond:wght@400;500;600&family=Poppins:wght@300;400;500;800&display=swap">
<style>
:root{
  --purple:#9c2b91;
  --purple-dark:#7d1f74;
  --orange:#e87a37;
  --blush:#fbf1f7;
  --charcoal:#3f3f44;
  --plum:#4b0b40;
  --ink:#2b2b2b;
  --muted:#555;
  --white:#fff;
  --serif:"Cormorant Garamond", Georgia, serif;
  --sans:"Poppins", Arial, sans-serif;
}
*{box-sizing:border-box;margin:0;padding:0}
html,body{width:1200px;height:4338px;overflow:hidden}
body{position:relative;background:var(--white);font-family:var(--sans);color:var(--ink)}
a{color:inherit}

/* header */
.site-header{position:absolute;left:0;top:0;width:1200px;height:78px;background:var(--white)}
.brand{position:absolute;left:22px;top:14px;display:flex;align-items:center;gap:10px}
.brand-dot{width:44px;height:44px;border-radius:50%;background:var(--purple)}
.brand-name{font-family:var(--serif);font-weight:600;font-size:32px;line-height:1;color:var(--charcoal);font-variant:small-caps;letter-spacing:.5px}
.brand-tag{font-family:var(--serif);font-size:13px;letter-spacing:3px;color:var(--charcoal);margin-top:2px;text-align:center}
.main-nav{position:absolute;left:443px;top:29px;display:flex;gap:40px;font-family:var(--serif);font-size:16px;font-weight:600}
.main-nav a{text-decoration:none;color:var(--ink)}
.main-nav a.active{color:var(--purple)}
.nav-cta{position:absolute;left:917px;top:21px;height:37px;width:236px;border-radius:20px;overflow:hidden;display:flex;font-family:var(--serif);font-size:13px;font-weight:600;color:var(--white);letter-spacing:.5px;box-shadow:0 2px 4px rgba(0,0,0,.2)}
.nav-cta span{display:flex;align-items:center;justify-content:center}
.nav-cta .appt{background:var(--orange);width:120px}
.nav-cta .contact{background:var(--purple);flex:1}

/* hero */
.hero{position:absolute;left:0;top:78px;width:1200px;height:565px;background:linear-gradient(110deg,#c9b5a3 0%,#e8e2dc 45%,#d9d3cd 70%,#b9a89a 100%)}
.hero-title{position:absolute;left:0;width:1200px;top:200px;text-align:center;font-family:var(--serif);font-size:66px;font-weight:500;font-variant:small-caps;color:var(--charcoal)}
.hero-sub{position:absolute;left:0;width:1200px;top:276px;text-align:center;font-family:var(--serif);font-size:27px;color:var(--charcoal)}
.btn{display:inline-flex;align-items:center;justify-content:center;font-family:var(--serif);font-weight:600;letter-spacing:1px;color:var(--white);background:var(--purple);box-shadow:0 3px 4px rgba(0,0,0,.3);text-transform:uppercase;text-decoration:none}
.hero .btn{position:absolute;left:502px;top:327px;width:145px;height:40px;font-size:16px}
.slider-dots{position:absolute;left:62px;top:236px;display:flex;flex-direction:column;gap:8px}
.slider-dots i{width:10px;height:10px;border:1px solid #fff;border-radius:50%}
.slider-dots i.on{background:var(--purple);border-color:var(--purple)}
.social-rail{position:absolute;left:1136px;top:84px;display:flex;flex-direction:column;gap:14px;align-items:center}
.social-rail i{width:25px;height:25px;border:1px solid var(--charcoal);border-radius:50%}
.social-rail .line{width:1px;height:60px;background:var(--charcoal)}
.scroll-label{position:absolute;left:1140px;top:320px;writing-mode:vertical-rl;font-size:13px;font-weight:500;letter-spacing:1px;color:var(--ink)}
.hero-band{position:absolute;left:0;top:643px;width:1200px;height:14px;background:var(--purple)}
.scroll-arrow{position:absolute;left:583px;top:620px;width:34px;height:56px;border-radius:17px;background:var(--white);border:2px solid var(--purple)}

/* section titles */
.section-title{position:absolute;left:0;width:1200px;display:flex;align-items:center;justify-content:center;gap:16px;font-family:var(--serif);font-variant:small-caps;font-size:46px;font-weight:500;color:var(--charcoal)}
.section-title .rule{width:150px;height:8px;border-top:2px solid var(--purple);border-bottom:2px solid var(--purple)}
.section-title.light{color:var(--white)}
.section-title.light .rule{border-color:var(--white)}

/* about */
.about{position:absolute;left:0;top:657px;width:1200px;height:685px;background:var(--blush)}
.about-copy{position:absolute;left:118px;top:172px;width:447px;text-align:justify;text-align-last:right;font-size:13.5px;line-height:23px;color:var(--ink)}
.about-copy p+p{margin-top:18px}
.about .btn{position:absolute;left:426px;top:546px;width:146px;height:44px;font-size:16px}
.about-photo{position:absolute;left:590px;top:151px;width:500px;height:452px;border:3px solid var(--orange);border-radius:6px;background:linear-gradient(135deg,#b8aca0,#e5dfd8 50%,#5a6a82)}

/* services */
.services{position:absolute;left:0;top:1342px;width:1200px;height:714px;background:var(--white)}
.service-card{position:absolute;top:270px;width:252px;height:278px;background:var(--white);border-radius:8px;box-shadow:0 3px 10px rgba(0,0,0,.22);text-align:center}
.service-photo{position:absolute;left:32px;top:-109px;width:188px;height:188px;border-radius:50%;border:5px solid var(--purple);background:linear-gradient(135deg,#d8cfc5,#8d7c6e)}
.service-card h3{margin-top:98px;font-family:var(--serif);font-size:21px;font-weight:500;color:var(--ink)}
.service-card p{margin:6px 22px 0;font-size:11px;line-height:20px;font-weight:300;color:var(--muted)}
.service-card a{display:block;margin-top:12px;font-family:var(--serif);font-size:13px;text-decoration:underline}
.services .btn{position:absolute;left:527px;top:581px;width:146px;height:44px;font-size:16px}

/* fees */
.fees-panel{position:absolute;left:111px;top:2056px;width:978px;height:572px;border-radius:28px;background:var(--orange)}
.fee-card{position:absolute;top:161px;width:373px;height:326px;background:var(--white);border-radius:6px;overflow:hidden;text-align:center;box-shadow:0 2px 6px rgba(0,0,0,.15)}
.fee-head{height:166px;background:var(--purple);color:var(--white);padding-top:22px}
.fee-head .kind{font-family:var(--serif);font-size:22px;font-weight:600}
.fee-head .plan{font-family:var(--sans);font-weight:800;font-size:38px;line-height:47px;margin-top:6px}
.fee-body .label{margin-top:24px;font-family:var(--serif);font-size:22px;font-weight:500}
.fee-body .amount{font-family:var(--serif);font-size:62px;line-height:56px;font-weight:500}
.fee-body .amount small{font-size:32px}
.fee-body .note{margin-top:12px;font-size:15px}

/* blog */
.blog{position:absolute;left:0;top:2718px;width:1200px;height:584px;background:var(--purple)}
.post-card{position:absolute;top:162px;width:526px;height:267px;background:var(--white);border-radius:10px;overflow:hidden;box-shadow:0 2px 6px rgba(0,0,0,.25)}
.post-photo{position:absolute;left:0;top:0;width:237px;height:267px;background:linear-gradient(135deg,#c9b8a6,#7e6f63)}
.post-text{position:absolute;left:253px;top:40px;width:258px}
.post-text h3{font-size:18.5px;font-weight:500;line-height:26px;color:var(--ink)}
.post-text p{margin-top:16px;font-size:13.5px;line-height:21px;font-weight:300;color:var(--ink)}
.post-text a{display:block;margin-top:14px;font-size:11px;font-weight:500;text-decoration:underline}
.blog .btn{position:absolute;left:527px;top:462px;width:146px;height:44px;font-size:16px;background:var(--orange)}

/* contact */
.contact-box{position:absolute;left:155px;top:3380px;width:480px;height:508px;background:var(--charcoal);border-radius:18px;color:var(--white)}
.contact-box .section-title{left:0;width:480px;top:42px;font-size:36px;color:var(--white)}
.contact-box .section-title .rule{width:76px;border-color:var(--white)}
.contact-row{position:absolute;left:80px;display:flex;gap:22px;align-items:flex-start}
.contact-icon{width:43px;height:43px;border-radius:50%;background:var(--purple);flex:none;display:flex;align-items:center;justify-content:center}
.contact-row .k{font-family:var(--serif);font-size:18px;font-weight:600}
.contact-row .v{font-size:16.5px;line-height:24px}
.social-chips{position:absolute;left:80px;top:404px;display:flex;gap:8px}
.social-chips i{width:43px;height:43px;border-radius:50%;background:var(--orange)}
.contact-form{position:absolute;left:662px;top:3440px;width:383px}
.field{height:60px;border-bottom:1.5px solid #666;padding:18px 0 0 18px;font-size:13px;color:var(--ink)}
.field.tall{height:126px}
.contact-form .btn{margin-top:30px;width:180px;height:45px;font-size:16px}

/* footer */
.footer-rule{position:absolute;left:0;top:3968px;width:1200px;height:9px;background:var(--orange)}
.site-footer{position:absolute;left:0;top:3977px;width:1200px;height:361px;background:var(--plum);color:var(--white)}
.site-footer .brand{left:112px;top:100px}
.site-footer .brand-name,.site-footer .brand-tag{color:var(--white)}
.footer-col{position:absolute;top:55px}
.footer-col h4{font-family:var(--serif);font-size:19px;font-weight:600;padding-bottom:10px;border-bottom:2px solid var(--orange);display:inline-block;width:52px;white-space:nowrap}
.footer-col ul{list-style:none;margin-top:14px}
.footer-col li{font-size:12px;line-height:23px}
.footer-divider{position:absolute;left:111px;top:274px;width:978px;height:1px;background:rgba(255,255,255,.35)}
.copyright{position:absolute;left:0;width:1200px;top:308px;text-align:center;font-size:15px}
.copyright a{color:var(--orange)}
</style>
</head>
<body>

<header class="site-header">
  <div class="brand">
    <span class="brand-dot"></span>
    <div><div class="brand-name">Dr Clara Hayes</div><div class="brand-tag">— CLINICAL PSYCHOLOGIST —</div></div>
  </div>
  <nav class="main-nav">
    <a class="active" href="#">Home</a><a href="#">About Us</a><a href="#">Services</a><a href="#">Testimonials</a><a href="#">Blog</a>
  </nav>
  <div class="nav-cta"><span class="appt">APPOINTMENT</span><span class="contact">CONTACT US</span></div>
</header>

<section class="hero" role="img" aria-label="Photo of a psychologist talking with a young girl in a bright therapy room">
  <h1 class="hero-title">Dr Clara Hayes</h1>
  <p class="hero-sub">CLINICAL PSYCHOLOGIST</p>
  <a class="btn" href="#">Contact Us</a>
  <div class="slider-dots"><i></i><i class="on"></i><i></i><i></i></div>
  <div class="social-rail"><i></i><i></i><i></i><i></i><span class="line"></span></div>
  <span class="scroll-label">SCROLL DOWN</span>
</section>
<div class="hero-band"></div>
<svg class="scroll-arrow" viewBox="0 0 34 56" aria-hidden="true"><path d="M17 14v28M10 35l7 8 7-8" fill="none" stroke="#2b2b2b" stroke-width="2"/></svg>

<section class="about">
  <h2 class="section-title" style="top:70px"><span class="rule"></span>About Us<span class="rule"></span></h2>
  <div class="about-copy">
    <p>Saerspiciatis undeasepoilse oklasdo mnis aidaste natus error sit voluptatem accusan tium doloremque laudantium, totam rem aperiam, ease aque ipaefdsa quae ab illo inventore veritatis ease quasi architecto beatae vitae dicta sunt explicabo. Nemo enim ipsam voluptatem quia volasdfupta sde sessitasese aspernatur autodit aut fugitsdsed quisaea consequuntur magni dolores eos qui ratione voluptatem sequi nesciunt.</p>
    <p>Kaosek oklasdo mnis aidaste natus error sit voluptatem accusan tium doloremque laudantium, totam rem aperiam, ease aque ipaefdsa quae ab illo inventore veritatis ease quasi architecto beatae vitasaee dicta susekont explicabo. Nemo enim ipsam voluptatem quia volasdfupta sde sessitasese aspernatur autodit aut fugitsdsed quisaea consequuntur magni dolores eos qui ratione voluptatem sequi nesciunt.</p>
  </div>
  <a class="btn" href="#">Learn More</a>
  <div class="about-photo" role="img" aria-label="Photo of a therapist listening to a smiling client seated on a sofa"></div>
</section>

<section class="services">
  <h2 class="section-title" style="top:62px"><span class="rule"></span>Our Services<span class="rule"></span></h2>
  <article class="service-card" style="left:173px">
    <div class="service-photo" role="img" aria-label="Photo of an individual counselling session"></div>
    <h3>Individual Counseling</h3>
    <p>Saerspiciatis aseusand seasepoilse oklasdo mnisfa aidaste natus error sesesit voluptatem accusan tiusm sdoloremque laudantium, totam resm apeam ease aque.</p>
    <a href="#">Learn More</a>
  </article>
  <article class="service-card" style="left:474px">
    <div class="service-photo" role="img" aria-label="Photo of a couples therapy session"></div>
    <h3>Couples Therapy</h3>
    <p>Saerspiciatis aseusand seasepoilse oklasdo mnisfa aidaste natus error sesesit voluptatem accusan tiusm sdoloremque laudantium, totam resm apeam ease aque.</p>
    <a href="#">Learn More</a>
  </article>
  <article class="service-card" style="left:775px">
    <div class="service-photo" role="img" aria-label="Photo of a family counselling session"></div>
    <h3>Family Counseling</h3>
    <p>Saerspiciatis aseusand seasepoilse oklasdo mnisfa aidaste natus error sesesit voluptatem accusan tiusm sdoloremque laudantium, totam resm apeam ease aque.</p>
    <a href="#">Learn More</a>
  </article>
  <a class="btn" href="#">View More</a>
</section>

<section class="fees-panel">
  <h2 class="section-title light" style="left:0;width:978px;top:70px;font-size:42px"><span class="rule"></span>Fees<span class="rule" style="width:112px"></span></h2>
  <div class="fee-card" style="left:93px">
    <div class="fee-head"><div class="kind">Overall Consulting Fees</div><div class="plan">Initial<br>One-Time</div></div>
    <div class="fee-body"><div class="label">Price</div><div class="amount">100 <small>US $</small></div></div>
  </div>
  <div class="fee-card" style="left:520px">
    <div class="fee-head"><div class="kind">Subscription Type</div><div class="plan">Monthly<br>Subscription</div></div>
    <div class="fee-body"><div class="label">Price</div><div class="amount">300 <small>US $</small></div><div class="note">Per Location</div></div>
  </div>
</section>

<section class="blog">
  <h2 class="section-title light" style="top:70px"><span class="rule"></span>Blog &amp; News<span class="rule"></span></h2>
  <article class="post-card" style="left:65px">
    <div class="post-photo" role="img" aria-label="Photo of a smiling family with a counsellor"></div>
    <div class="post-text">
      <h3>Haerspiciatis unde omnis iste natus errorsait.</h3>
      <p>Kallo inventore veritatis et quasi architecto beatae vitae dicta sunt explicabo. Nemo enim ipsam voluptatem quia voluptas sit aspernatur aut odit aut.</p>
      <a href="#">Learn More</a>
    </div>
  </article>
  <article class="post-card" style="left:607px">
    <div class="post-photo" role="img" aria-label="Photo of a young man talking with a counsellor"></div>
    <div class="post-text">
      <h3>Haerspiciatis unde omnis iste natus errorsait.</h3>
      <p>Kallo inventore veritatis et quasi architecto beatae vitae dicta sunt explicabo. Nemo enim ipsam voluptatem quia voluptas sit aspernatur aut odit aut.</p>
      <a href="#">Learn More</a>
    </div>
  </article>
  <a class="btn" href="#">View More</a>
</section>

<section class="contact-box">
  <h2 class="section-title"><span class="rule"></span>Contact Us<span class="rule"></span></h2>
  <div class="contact-row" style="top:142px">
    <span class="contact-icon"><svg width="18" height="22" viewBox="0 0 18 22"><path d="M9 1a8 8 0 0 0-8 8c0 6 8 12 8 12s8-6 8-12a8 8 0 0 0-8-8z" fill="#fff"/><circle cx="9" cy="9" r="3" fill="#9c2b91"/></svg></span>
    <div><div class="k">Address</div><div class="v">52 Wattle Grove Lane, Suite 3<br>Parramatta NSW 2150</div></div>
  </div>
  <div class="contact-row" style="top:238px">
    <span class="contact-icon"><svg width="20" height="20" viewBox="0 0 20 20"><path d="M4 2l4 4-2 3c1 2 3 4 5 5l3-2 4 4-2 3C9 19 1 11 2 4z" fill="#fff"/></svg></span>
    <div><div class="k">Call Us</div><div class="v">+61 (02) 5550 1429</div></div>
  </div>
  <div class="contact-row" style="top:310px">
    <span class="contact-icon"><svg width="22" height="16" viewBox="0 0 22 16"><rect x="1" y="1" width="20" height="14" fill="#fff"/><path d="M1 1l10 8 10-8" fill="none" stroke="#9c2b91" stroke-width="1.5"/></svg></span>
    <div><div class="k">Email</div><div class="v">hello@clarahayes.example</div></div>
  </div>
  <div class="social-chips"><i></i><i></i><i></i><i></i></div>
</section>

<form class="contact-form">
  <div class="field">Your Name</div>
  <div class="field">Email</div>
  <div class="field">Phone Number</div>
  <div class="field tall">Message</div>
  <span class="btn">Send Message</span>
</form>

<div class="footer-rule"></div>
<footer class="site-footer">
  <div class="brand">
    <span class="brand-dot" style="background:var(--orange)"></span>
    <div><div class="brand-name">Dr Clara Hayes</div><div class="brand-tag">— CLINICAL PSYCHOLOGIST —</div></div>
  </div>
  <div class="footer-col" style="left:540px"><h4>Quick Links</h4><ul><li>Home</li><li>About Us</li><li>Services</li><li>Testimonials</li><li>Blog</li><li>Contact Us</li></ul></div>
  <div class="footer-col" style="left:734px"><h4>Links</h4><ul><li>Our History</li><li>News &amp; Events</li><li>Blog</li><li>Customer Reviews</li></ul></div>
  <div class="footer-col" style="left:913px"><h4>Support</h4><ul><li>Team</li><li>About Us</li><li>Careers</li><li>Our Values</li><li>Data Security</li></ul></div>
  <div class="footer-divider"></div>
  <p class="copyright">© 2024 <a href="#">clarahayes.</a> All Rights Reserved.</p>
</footer>

</body>
</html>
```